Coastline Premier Retreats Business Card Design

Design a business card for Coastline Premier Retreats. Look at the website for colors and reference. Card should have logo, name, title, office number, mobile number, email, URL and a tagline like, "Luxury Hotel & Resort Email Marketing" (This might change).

https://www.coastlinepremierretreats.example

The rest I will leave up to your imagination.

Contact Information for Business Card

Logo, name, title, office number, mobile number, email, URL and a tagline like, "Luxury Hotel & Resort Email Marketing" (This might change).

```html
<!DOCTYPE html>
<html lang="en">
<head>
<meta charset="utf-8">
<title>Coastline Premier Retreats – Business Card</title>
<link href="https://fonts.googleapis.com/css2?family=Arimo:wght@400;700&display=swap" rel="stylesheet">
<style>
  :root {
    --backdrop: #d4d7d8;
    --card-white: #fbfbfa;
    --brand-orange: #e96d13;
    --ink-dark: #1e1e1e;
    --ink-grey: #505050;
    --on-orange: #fbf4ee;
  }
  * { box-sizing: border-box; margin: 0; padding: 0; }
  html, body {
    width: 1200px; height: 829px; overflow: hidden;
    background: var(--backdrop);
    font-family: "Arimo", Arial, sans-serif;
  }
  .stage { position: relative; width: 1200px; height: 829px; }
  .card {
    position: absolute; top: 262px;
    width: 540px; height: 309px;
    box-shadow: 0 10px 24px rgba(0,0,0,0.18);
  }
  .card--front { left: 40px; background: var(--card-white); }
  .card--back { left: 620px; background: var(--brand-orange); }

  /* front side */
  .frame { position: absolute; inset: 0; }
  .brand {
    position: absolute; left: 36px; top: 104px; width: 215px;
    display: flex; align-items: center; gap: 8px;
    color: var(--ink-dark);
  }
  .brand__square { width: 12px; height: 12px; background: var(--brand-orange); flex: none; }
  .brand__name { font-weight: 700; font-size: 17px; letter-spacing: 0.5px; line-height: 1.2; text-transform: uppercase; }
  .divider {
    position: absolute; left: 272px; top: 78px; width: 1.5px; height: 136px;
    background: var(--brand-orange);
  }
  .contact { position: absolute; left: 292px; top: 78px; color: var(--ink-grey); font-size: 11.5px; line-height: 1.45; }
  .contact__name { color: var(--brand-orange); font-weight: 700; font-size: 19px; letter-spacing: 0.5px; line-height: 1.1; }
  .contact__title { margin-bottom: 8px; font-size: 12px; }
  .contact__address { margin-bottom: 6px; }
  .contact__row { display: flex; align-items: center; gap: 7px; }
  .contact__row svg { width: 10px; height: 10px; flex: none; fill: var(--brand-orange); }
  .tagline {
    position: absolute; left: 0; right: 0; bottom: 20px;
    text-align: center; font-size: 12px; color: var(--ink-grey);
  }

  /* back side */
  .back-brand {
    position: absolute; inset: 0;
    display: flex; align-items: center; justify-content: center; gap: 14px;
    color: var(--on-orange);
  }
  .back-brand__square { width: 20px; height: 20px; background: var(--on-orange); }
  .back-brand__name { font-weight: 700; font-size: 27px; letter-spacing: 1.5px; line-height: 1.15; text-transform: uppercase; }
</style>
</head>
<body>
<main class="stage">
  <section class="card card--front">
    <svg class="frame" width="540" height="309" viewBox="0 0 540 309" aria-hidden="true">
      <polyline points="140,286 20,286 20,20 520,20 520,286 400,286" fill="none" stroke="#e96d13" stroke-width="1.5"/>
    </svg>
    <div class="brand">
      <span class="brand__square"></span>
      <span class="brand__name">Coastline Premier<br>Retreats</span>
    </div>
    <div class="divider"></div>
    <div class="contact">
      <p class="contact__name">DANIEL REYES</p>
      <p class="contact__title">CEO/Founder</p>
      <p class="contact__address">Po Box, 48 Harbor Lane<br>Seaview, CA 90210</p>
      <p class="contact__row"><svg viewBox="0 0 10 10"><rect x="2.5" y="0.5" width="5" height="9" rx="1"/></svg>555.014.2200</p>
      <p class="contact__row"><svg viewBox="0 0 10 10"><path d="M1 3c0-1 1-2 4-2s4 1 4 2v1H7V3H3v1H1zM2 5h6l1 4H1z"/></svg>+1 555 019 4471</p>
      <p class="contact__row"><svg viewBox="0 0 10 10"><path d="M0 2h10v6H0zM0.8 2.6 5 5.6l4.2-3" stroke="#fbfbfa" stroke-width="0.8"/></svg>info@coastlinepremierretreats.example</p>
      <p class="contact__row"><svg viewBox="0 0 10 10"><circle cx="5" cy="5" r="4.5"/><path d="M0.5 5h9M5 0.5c-2 2.5-2 6.5 0 9M5 0.5c2 2.5 2 6.5 0 9" stroke="#fbfbfa" stroke-width="0.7" fill="none"/></svg>www.coastlinepremierretreats.example</p>
    </div>
    <p class="tagline">Luxury Hotel &amp; Resort Email Marketing</p>
  </section>

  <section class="card card--back">
    <div class="back-brand">
      <span class="back-brand__square"></span>
      <span class="back-brand__name">Coastline Premier<br>Retreats</span>
    </div>
  </section>
</main>
</body>
</html>
```